Web design for financial services

A modern web design of financial services (brokerage firm)
Req.s and technology tags :
- Very mobile friendly.
- One paged with some inner pages.
- Animated sticky header .
- Member login area for e-trade.
- Support RTL language.
- HTML & CSS.

The logo will be Home link
• MPTR :
WHO WE ARE
Content :
i) Board of Directors
ii) Mission Statement
iii) Corporate Values
iv) Regulations
• Financial Services :
WHAT WE DO
Content:
i) Electronic trading
ii) Trading desk
iii) Institutional
iv) Investors Education
• News
• Market Tools
• Forms---- opens new page
• Careers---- opens new page
• Contact Us----opens new page

The website is :
http://www.mptr-doha-example.com/

The logo need some changes to be more modern and impressively , but with keeping same structure .

Some related websites :
https://www.lv-bourse.example/

financial market

Financial Service

Coded - Design and coding required

2 page

• same fonts of http://www.kwdholdings.example/

• - Very mobile friendly.
• - One paged with some inner pages.
• - Animated sticky header .
• - Member login area for e-trade.
• - Support RTL language.
• - HTML & CSS.
• Slider , some Qatari theme,
• i like the video inside the home page
• ex :http://www.kwdholdings.example/

```html
<!DOCTYPE html>
<html lang="en">
<head>
<meta charset="utf-8">
<title>MPTR — Majlis Pearl Trade &amp; Reserve</title>
<link href="https://fonts.googleapis.com/css2?family=Open+Sans:wght@400;600;700;800&display=swap" rel="stylesheet">
<style>
:root{
  --red:#9b1c20;
  --red-dark:#7d1417;
  --ink:#222;
  --muted:#666;
  --soft:#ececec;
  --line:#d6d6d6;
  --night:#1e1e1e;
  --white:#fff;
}
*{box-sizing:border-box;margin:0;padding:0}
html,body{width:1200px;height:4600px;overflow:hidden}
body{font-family:"Open Sans",Arial,sans-serif;color:var(--ink);background:var(--white);position:relative}
section,header,footer{position:absolute;left:0;width:1200px}
.abs{position:absolute}
.heading{font-weight:800;color:var(--red);font-size:26px;letter-spacing:.5px}
.heading.center{text-align:center;width:100%}
.heading.rule::after{content:"";display:block;width:60px;height:3px;background:var(--red);margin-top:10px}
.heading.center.rule::after{margin:10px auto 0}
.text{font-size:13px;line-height:22px;color:var(--muted)}
.btn{display:inline-block;font-size:12px;font-weight:700;padding:10px 20px;background:var(--red);color:var(--white);text-transform:uppercase;letter-spacing:.5px;white-space:nowrap}
.btn.ghost{background:var(--white);color:var(--ink);border:1px solid #999}
.subhead{font-size:17px;font-weight:700;color:var(--red);display:flex;align-items:center;gap:10px;margin-bottom:10px;white-space:nowrap}
.subhead i{width:14px;height:14px;background:var(--red);display:inline-block;flex:none}

/* header / hero */
.hero{top:0;height:640px;background:linear-gradient(180deg,#1a1f2a 0%,#2b3442 45%,#3b4048 70%,#2b2b2e 100%)}
.hero-photo{position:absolute;inset:0;background:radial-gradient(ellipse at 50% 35%,rgba(120,140,170,.35),transparent 60%),linear-gradient(90deg,rgba(0,0,0,.35),transparent 30%,transparent 70%,rgba(0,0,0,.35))}
.brand{position:absolute;left:40px;top:28px;display:flex;align-items:center;gap:10px;color:var(--white);font-weight:800;font-size:26px}
.brand .dot{width:30px;height:30px;border-radius:50%;background:var(--red)}
.topbar{position:absolute;right:40px;top:18px;display:flex;gap:8px}
.topbar span{font-size:11px;font-weight:700;color:var(--white);padding:6px 12px}
.topbar .trade{background:var(--red)}
.topbar .lang{border:1px solid rgba(255,255,255,.5)}
.nav{position:absolute;right:40px;top:88px;display:flex;gap:34px;font-size:12px;font-weight:700;color:var(--white)}
.play{position:absolute;left:560px;top:250px;width:80px;height:80px;border-radius:50%;border:3px solid rgba(255,255,255,.85)}
.hero-title{position:absolute;top:370px;width:100%;text-align:center;color:var(--white);font-size:60px;font-weight:600}
.hero-sub{position:absolute;top:455px;width:100%;text-align:center;color:var(--white);font-size:30px;font-weight:600}

/* who we are */
.who{top:640px;height:520px}
.who-photo{position:absolute;right:0;top:20px;width:500px;height:412px;background:linear-gradient(135deg,#c9a78a,#8a6d5a 50%,#e3e0dc);clip-path:polygon(14% 0,100% 0,100% 100%,0 100%)}
.who .heading{left:100px;top:92px}
.who .intro{left:100px;top:150px;width:610px}
.col{width:290px}

/* what we do */
.what{top:1160px;height:560px;background:var(--soft)}
.what-photo{position:absolute;left:0;top:20px;width:480px;height:420px;background:linear-gradient(135deg,#d9d3c9,#8b8f95 55%,#5a4d44);clip-path:polygon(0 0,100% 0,86% 100%,0 100%)}
.what .heading{left:520px;top:112px}
.what .intro{left:520px;top:170px;width:600px}

/* services */
.services{top:1720px;height:500px}
.service{position:absolute;top:240px;width:260px;text-align:center}
.service svg{display:block;margin:0 auto}
.service p{font-size:12px;font-weight:700;color:var(--ink);margin-top:18px;line-height:18px}

/* news */
.news{top:2220px;height:740px;background:var(--soft)}
.card{position:absolute;top:120px;width:320px}
.card .photo{height:220px}
.date{position:absolute;left:0;top:150px;width:60px;height:70px;background:var(--red);color:var(--white);text-align:center;font-size:12px;font-weight:700;padding-top:14px;line-height:20px}
.card h3{font-size:17px;font-weight:700;text-align:center;margin:40px 0 12px}
.card .text{text-align:center;font-size:12px;line-height:19px}
.card .btn{position:absolute;left:50%;transform:translateX(-50%);top:380px}

/* market index */
.index{top:2960px;height:400px}

/* partners */
.partners{top:3380px;height:160px;background:var(--soft)}
.badge{position:absolute;top:50px;width:110px;height:62px;border:2px solid #bbb;border-radius:8px;background:var(--white)}

/* tools */
.tools{top:3560px;height:600px}
.tool{position:absolute;top:160px;width:384px}
.tool .photo{height:292px;position:relative}
.tool .label{position:absolute;bottom:0;left:0;right:0;height:44px;background:rgba(0,0,0,.75);color:var(--white);font-weight:700;font-size:15px;text-align:center;line-height:44px}
.tool .text{margin-top:16px;font-size:12px;line-height:19px}

/* footer */
.footer{top:4160px;height:440px;background:var(--night);color:#ddd}
.fbrand{position:absolute;left:100px;top:100px;display:flex;align-items:center;gap:12px;font-weight:800;font-size:36px;color:var(--white)}
.fbrand .ring{width:48px;height:48px;border-radius:50%;border:3px solid var(--white)}
.fhead{font-size:15px;font-weight:800;color:var(--white);margin-bottom:20px}
.flist{list-style:none;font-size:13px;line-height:28px}
.flist li::before{content:"›";margin-right:8px;color:#aaa}
.soc{list-style:none;font-size:13px}
.soc li{display:flex;align-items:center;gap:12px;margin-bottom:14px}
.soc li i{width:26px;height:26px;border-radius:50%;background:#555;display:inline-block}
.contact{font-size:13px;line-height:20px}
.contact .row{display:flex;gap:14px;margin-bottom:18px}
.contact b{color:var(--white);display:block}
.copy{position:absolute;bottom:0;left:0;width:100%;height:48px;border-top:1px solid #333;text-align:center;line-height:48px;font-size:12px;color:#bbb}
</style>
</head>
<body>

<header class="hero">
  <div class="hero-photo" role="img" aria-label="Night skyline of Doha towers behind the hero text"></div>
  <div class="brand"><span class="dot"></span>MPTR</div>
  <div class="topbar"><span class="trade">MPTR E-TRADE</span><span class="lang">ENGLISH ▾</span></div>
  <nav class="nav"><span>MPTR</span><span>FINANCIAL SERVICE</span><span>NEWS</span><span>MARKET TOOL</span><span>FORMS</span><span>CAREERS</span><span>CONTACT US</span></nav>
  <div class="play">
    <svg width="74" height="74" viewBox="0 0 74 74"><path d="M30 24 L52 37 L30 50 Z" fill="#fff"/></svg>
  </div>
  <h1 class="hero-title">Majlis Pearl Trade &amp; Reserve</h1>
  <p class="hero-sub">We are a financial services company</p>
</header>

<section class="who">
  <div class="who-photo" role="img" aria-label="Two colleagues reviewing a laptop together in an office"></div>
  <h2 class="heading rule abs">WHO WE ARE</h2>
  <p class="text abs intro">MPTR is a private Qatari company that aims to provide secure and technologically advanced methods of trading to its clients. These facilities enable clients to trade faster, more secure and private, making this strategy in our minds with this online portal we begin.</p>
  <div class="abs col" style="left:100px;top:280px">
    <div class="subhead"><i></i>Our Company</div>
    <p class="text">MPTR is a private Qatari company that aims to provide secure and technologically advanced methods of trading to its clients.</p>
  </div>
  <div class="abs col" style="left:420px;top:280px">
    <div class="subhead"><i></i>Our Vision</div>
    <p class="text">We intend to optimize all company resources to position ourselves as a unique competitive business model with the goal of generating highly competitive returns.</p>
  </div>
  <span class="btn abs" style="left:100px;top:432px">About MPTR</span>
</section>

<section class="what">
  <div class="what-photo" role="img" aria-label="Businessman reading documents at a desk"></div>
  <h2 class="heading rule abs">WHAT WE DO</h2>
  <p class="text abs intro">We intend to optimize all company resources to position ourselves as an unique competitive business model with the goal of generating highly competitive returns for our clients and shareholders, by providing accurate, rapid and reliable order execution, attractive financial products and services, sophisticated customer service.</p>
  <div class="abs col" style="left:520px;top:296px">
    <div class="subhead"><i></i>Trading Account Registration</div>
    <p class="text">MPTR is a private Qatari company that aims to provide secure and technologically advanced methods of trading to its clients.</p>
  </div>
  <div class="abs col" style="left:840px;top:296px">
    <div class="subhead"><i></i>Electronic Registration</div>
    <p class="text">MPTR is a private Qatari company that aims to provide secure and technologically advanced methods of trading to its clients.</p>
  </div>
  <span class="btn abs" style="left:520px;top:450px">Read More</span>
</section>

<section class="services">
  <h2 class="heading center rule abs" style="top:80px">OUR SERVICES</h2>
  <p class="text abs" style="left:250px;top:150px;width:700px;text-align:center">We intend to optimize all company resources to position ourselves as an unique competitive business model with the goal of generating highly competitive returns for our clients and shareholders, by providing accurate, rapid services.</p>
  <div class="service" style="left:140px">
    <svg width="180" height="180" viewBox="0 0 180 180">
      <polygon points="90,8 162,48 162,132 90,172 18,132 18,48" fill="none" stroke="#9b1c20" stroke-width="14"/>
      <polygon points="90,30 142,60 142,120 90,150 38,120 38,60" fill="#fff" stroke="#ccc" stroke-width="2"/>
      <rect x="62" y="100" width="10" height="20" fill="#9b1c20"/><rect x="80" y="86" width="10" height="34" fill="#9b1c20"/><rect x="98" y="74" width="10" height="46" fill="#9b1c20"/>
      <path d="M58 88 L78 72 L92 80 L120 58" fill="none" stroke="#444" stroke-width="3"/>
    </svg>
    <p>TRADING ACCOUNT<br>REGISTRATION/NEW SERVICES</p>
  </div>
  <div class="service" style="left:470px">
    <svg width="180" height="180" viewBox="0 0 180 180">
      <polygon points="90,8 162,48 162,132 90,172 18,132 18,48" fill="none" stroke="#9b1c20" stroke-width="14"/>
      <polygon points="90,30 142,60 142,120 90,150 38,120 38,60" fill="#fff" stroke="#ccc" stroke-width="2"/>
      <rect x="58" y="62" width="64" height="56" rx="4" fill="none" stroke="#9b1c20" stroke-width="4"/>
      <circle cx="90" cy="82" r="9" fill="#9b1c20"/><rect x="74" y="96" width="32" height="8" fill="#9b1c20"/>
    </svg>
    <p>ELECTRONIC<br>REGISTRATION</p>
  </div>
  <div class="service" style="left:800px">
    <svg width="180" height="180" viewBox="0 0 180 180">
      <polygon points="90,8 162,48 162,132 90,172 18,132 18,48" fill="none" stroke="#9b1c20" stroke-width="14"/>
      <polygon points="90,30 142,60 142,120 90,150 38,120 38,60" fill="#fff" stroke="#ccc" stroke-width="2"/>
      <rect x="62" y="58" width="46" height="62" fill="none" stroke="#9b1c20" stroke-width="4"/>
      <path d="M70 74 H100 M70 86 H100 M70 98 H90" stroke="#444" stroke-width="3"/>
      <path d="M100 112 L122 90 L128 96 L106 118 Z" fill="#444"/>
    </svg>
    <p>DEPOSIT &amp; WITHDRAW STOCKS<br>FROM &amp; TO CENTRAL DEPOSITARY</p>
  </div>
</section>

<section class="news">
  <h2 class="heading center rule abs" style="top:40px">IN THE NEWS</h2>
  <article class="card" style="left:100px">
    <div class="photo" role="img" aria-label="Hands signing paperwork on a desk" style="background:linear-gradient(135deg,#b9c2cc,#6f7884)"></div>
    <div class="date">JAN<br>17</div>
    <h3>Companies And Other Entities</h3>
    <p class="text">Filling out a new investor's application form to get a NIN number. Submission of the following documents along with the application form.</p>
    <span class="btn">Read More</span>
  </article>
  <article class="card" style="left:440px">
    <div class="photo" role="img" aria-label="Team meeting around a table with laptops" style="background:linear-gradient(135deg,#d6dde4,#7e8a97)"></div>
    <div class="date">DEC<br>21</div>
    <h3>How Can I Start Trading Online?</h3>
    <p class="text">Filling out a new investor's application form to get a NIN number. Submission of the following documents along with the application form.</p>
    <span class="btn ghost">Read More</span>
  </article>
  <article class="card" style="left:780px">
    <div class="photo" role="img" aria-label="Colleagues discussing charts on a tablet" style="background:linear-gradient(135deg,#c7ccd2,#5f6670)"></div>
    <div class="date">DEC<br>14</div>
    <h3>What Are The Deposit Procedures?</h3>
    <p class="text">Filling out a new investor's application form to get a NIN number. Submission of the following documents along with the application form.</p>
    <span class="btn ghost">Read More</span>
  </article>
</section>

<section class="index">
  <h2 class="heading center rule abs" style="top:70px">MARKET INDEX</h2>
  <p class="text abs" style="left:150px;top:140px;width:900px;text-align:center">Majlis Pearl Trade &amp; Reserve is a private Qatari company that aims to provide secure and technologically advanced methods of trading to its clients. These facilities enable clients to trade faster, more secure and private. Filling out a new investor's application form to get a NIN number. Submission of the following documents along with the application form. Original and copy of commercial registration.</p>
  <span class="btn abs" style="left:472px;top:240px">Read More</span>
  <span class="btn ghost abs" style="left:604px;top:240px">Contact Us</span>
</section>

<section class="partners">
  <svg class="abs" style="left:30px;top:66px" width="20" height="30" viewBox="0 0 20 30"><path d="M16 2 L4 15 L16 28" fill="none" stroke="#999" stroke-width="3"/></svg>
  <div class="badge" style="left:105px"></div>
  <div class="badge" style="left:255px"></div>
  <div class="badge" style="left:405px"></div>
  <div class="badge" style="left:545px"></div>
  <div class="badge" style="left:685px"></div>
  <div class="badge" style="left:835px"></div>
  <div class="badge" style="left:985px"></div>
  <svg class="abs" style="left:1150px;top:66px" width="20" height="30" viewBox="0 0 20 30"><path d="M4 2 L16 15 L4 28" fill="none" stroke="#999" stroke-width="3"/></svg>
</section>

<section class="tools">
  <h2 class="heading center rule abs" style="top:50px">MARKET TOOLS</h2>
  <div class="tool" style="left:12px">
    <div class="photo" role="img" aria-label="Business team meeting around a table" style="background:linear-gradient(135deg,#9aa3ad,#3e444c)"><div class="label">MOST ACTIVE COMPANY</div></div>
    <p class="text">Letter from board of directors or power of attorney from the person whose authorised to trade on behalf of company.</p>
  </div>
  <div class="tool" style="left:408px">
    <div class="photo" style="background:var(--red)">
      <svg class="abs" style="left:152px;top:78px" width="80" height="80" viewBox="0 0 80 80"><circle cx="40" cy="40" r="38" fill="#fff"/><circle cx="40" cy="32" r="9" fill="#9b1c20"/><path d="M24 58 Q40 40 56 58 Z" fill="#9b1c20"/></svg>
      <div class="abs" style="top:182px;width:100%;text-align:center;color:#fff;font-size:20px;font-weight:800">TOP GAINER</div>
    </div>
    <p class="text">Letter from board of directors or power of attorney from the person whose authorised to trade on behalf of company.</p>
  </div>
  <div class="tool" style="left:804px">
    <div class="photo" role="img" aria-label="Person working on a laptop with a calculator" style="background:linear-gradient(135deg,#c9bfb3,#6e655c)"><div class="label">TOP LOSER</div></div>
    <p class="text">Letter from board of directors or power of attorney from the person whose authorised to trade on behalf of company.</p>
  </div>
</section>

<footer class="footer">
  <div class="fbrand"><span class="ring"></span>MPTR</div>
  <div class="abs" style="left:328px;top:80px">
    <div class="fhead">QUICK LINKS</div>
    <ul class="flist"><li>Home</li><li>MPTR</li><li>Financial Services</li><li>News</li><li>Market Tool</li><li>Forms</li></ul>
  </div>
  <div class="abs" style="left:520px;top:120px">
    <ul class="flist"><li>Careers</li><li>Contact Us</li><li>Disclaimer</li></ul>
  </div>
  <div class="abs" style="left:660px;top:80px">
    <div class="fhead">SOCIAL MEDIA</div>
    <ul class="soc"><li><i></i>Circlefeed</li><li><i></i>Chirpline</li><li><i></i>Pinboardly</li><li><i></i>Workwire</li></ul>
  </div>
  <div class="abs contact" style="left:888px;top:80px">
    <div class="fhead">CONTACT US</div>
    <div class="row"><svg width="26" height="26" viewBox="0 0 26 26"><circle cx="13" cy="13" r="13" fill="#555"/><path d="M13 6 a5 5 0 0 1 5 5 c0 4 -5 9 -5 9 s-5 -5 -5 -9 a5 5 0 0 1 5 -5z" fill="#fff"/></svg><div><b>ADDRESS:</b>First Floor, Corniche Tower<br>Doha</div></div>
    <div class="row"><svg width="26" height="26" viewBox="0 0 26 26"><circle cx="13" cy="13" r="13" fill="#555"/><path d="M9 7 l3 0 1 4 -2 1 a8 8 0 0 0 4 4 l1 -2 4 1 0 3 c-7 1 -12 -4 -11 -11z" fill="#fff"/></svg><div><b>PHONE:</b>Phone: +974 4000 1234</div></div>
    <div class="row"><svg width="26" height="26" viewBox="0 0 26 26"><circle cx="13" cy="13" r="13" fill="#555"/><rect x="7" y="9" width="12" height="9" fill="none" stroke="#fff" stroke-width="1.5"/><path d="M7 9 L13 14 L19 9" fill="none" stroke="#fff" stroke-width="1.5"/></svg><div><b>Mail:</b>info@mptr-doha-example.com</div></div>
  </div>
  <div class="copy">Copyright © 2017 MPTR . All Right Reserved</div>
</footer>

</body>
</html>
```